New Business Card Design Project

Use the flyer uploaded and website www.brightoakbuilders.com for inspiration.
List Our Services on Backside of business cards
Marcus Delling
Harborline Builders Inc.
Licensed General Contractors
858-471-6093

Contact Information for Business Card

Use the flyer uploaded and website www.brightoakbuilders.com for inspiration. List Our Services on Backside of business cards Marcus Delling Harborline Builders Inc. Licensed General Contractors 858-471-6093

```html
<!DOCTYPE html>
<html lang="en">
<head>
<meta charset="utf-8">
<title>Harborline Builders – Business Cards</title>
<link href="https://fonts.googleapis.com/css2?family=Lato:wght@400;700;900&display=swap" rel="stylesheet">
<style>
  :root{
    --bg:#1d1c1d;
    --card:#1f2022;
    --card-edge:#3c86d4;
    --silver:#e4e4e4;
    --silver-dim:#bdbdbd;
    --text:#d8d8d8;
  }
  *{margin:0;padding:0;box-sizing:border-box}
  html,body{width:1200px;height:939px;overflow:hidden;background:var(--bg)}
  body{position:relative;font-family:"Lato",sans-serif;color:var(--text)}
  .card{
    position:absolute;width:520px;height:297px;border-radius:18px;
    background:linear-gradient(160deg,#242527 0%,var(--card) 60%,#1a1b1c 100%);
    border-bottom:4px solid var(--card-edge);border-left:2px solid var(--card-edge);
    box-shadow:0 14px 30px rgba(0,0,0,.55);
  }
  .card--services{left:110px;top:120px}
  .card--contact{left:570px;top:500px}

  .brand{position:absolute;left:0;right:0;top:92px;text-align:center}
  .brand__name{font-size:30px;font-weight:400;letter-spacing:2px;color:var(--silver);text-transform:uppercase}
  .brand__tagline{margin-top:6px;font-size:12px;letter-spacing:8px;color:var(--silver-dim)}
  .services{position:absolute;left:0;right:0;top:196px;text-align:center;font-size:12.5px;font-weight:700;letter-spacing:.8px;line-height:1.75;color:var(--silver)}

  .person{position:absolute;left:40px;top:38px}
  .person__name{font-size:25px;font-weight:900;letter-spacing:.5px;color:var(--silver)}
  .person__title{font-size:15px;color:var(--silver-dim);margin-top:2px}
  .contacts{position:absolute;left:40px;top:112px;list-style:none;font-size:14px;line-height:25px;color:var(--text)}
  .contacts li{display:flex;align-items:center;gap:10px}
  .contacts svg{width:12px;height:12px;fill:none;stroke:var(--silver-dim);stroke-width:1.6}
  .contacts .phone{font-weight:700;color:var(--silver)}
  .license{position:absolute;left:40px;top:232px;font-size:14px;font-weight:700;color:var(--silver)}
</style>
</head>
<body>
  <section class="card card--services">
    <div class="brand">
      <div class="brand__name">Harborline Builders</div>
      <div class="brand__tagline">BUILD YOUR DREAM</div>
    </div>
    <div class="services">
      PAINTING | FLOORING | KITCHENS | BATHROOMS<br>
      ENERGY EFFICIENT UPGRADES | CUSTOM RENOVATIONS
    </div>
  </section>

  <section class="card card--contact">
    <div class="person">
      <div class="person__name">MARCUS DELLING</div>
      <div class="person__title">Licensed General Contractors</div>
    </div>
    <ul class="contacts">
      <li><svg viewBox="0 0 12 12"><path d="M6 11S2 6.8 2 4.4a4 4 0 0 1 8 0C10 6.8 6 11 6 11z"/><circle cx="6" cy="4.4" r="1.3"/></svg>Harborline Builders Inc.</li>
      <li><svg viewBox="0 0 12 12"><path d="M2.5 1.5l2 .3.7 2.2-1.2 1a6 6 0 0 0 3 3l1-1.2 2.2.7.3 2A1.5 1.5 0 0 1 9 10.5 8.5 8.5 0 0 1 1.5 3a1.5 1.5 0 0 1 1-1.5z"/></svg><span><span class="phone">858-471-6093</span> Call/Text</span></li>
      <li><svg viewBox="0 0 12 12"><rect x="1" y="2.5" width="10" height="7"/><path d="M1 2.5l5 4 5-4"/></svg>info@brightoakbuilders.com</li>
      <li><svg viewBox="0 0 12 12"><circle cx="6" cy="6" r="5"/><path d="M1 6h10M6 1c-2.5 2.8-2.5 7.2 0 10M6 1c2.5 2.8 2.5 7.2 0 10"/></svg>brightoakbuilders.com</li>
    </ul>
    <div class="license">CSLB LIC: 1047215</div>
  </section>
</body>
</html>
```